BrindleStaffing Business Card Design

We are a staffing company finding positions for dedicated nurses and physicians.

Target Market(s)

Business Professionals

Industry/Entity Type

Staffing

Contact Information for Business Card

Gordon Pratley
Chairman
417 39th Avenue South
SAINT PETERSBURG FL 33712
813-555-4172 Mobile
813-555-8036 Fax
gpratley@brindlestaffing.com
www.brindlestaffing.com

Font styles to use
Sans Serif

Colors
fbee3e
f04a50
f37122

Requirements
Must have
• Logo Attached, see colors below. We'd like to see Yellow, Orange and Red.

```html
<!DOCTYPE html>
<html lang="en">
<head>
<meta charset="utf-8">
<title>BrindleStaffing Business Card</title>
<link href="https://fonts.googleapis.com/css2?family=Roboto:wght@400;500;700&display=swap" rel="stylesheet">
<style>
  :root {
    --page-bg: #e4e4e4;
    --card-light: #ffffff;
    --card-dark: #1b1c1e;
    --brand-yellow: #fbee3e;
    --brand-orange: #f37122;
    --brand-red: #f04a50;
    --text-grey: #4a4a4a;
    --text-light: #f2f2f2;
  }
  * { box-sizing: border-box; margin: 0; padding: 0; }
  html, body {
    width: 1125px; height: 1200px; overflow: hidden;
    background: var(--page-bg);
    font-family: "Roboto", Arial, sans-serif;
  }
  .card {
    position: absolute; left: 171px; width: 826px; height: 472px;
    border-radius: 24px; overflow: hidden;
  }
  .card--front { top: 106px; background: var(--card-light); }
  .card--back { top: 640px; background: var(--card-dark); }

  .wordmark {
    position: absolute; left: 0; right: 0;
    display: flex; justify-content: center; align-items: center; gap: 14px;
    font-weight: 700; font-size: 54px; line-height: 1;
    color: var(--brand-orange);
  }
  .wordmark__dot {
    width: 16px; height: 16px; border-radius: 50%; background: var(--brand-red);
  }
  .card--front .wordmark { top: 94px; }
  .card--back .wordmark { top: 214px; }

  .person { position: absolute; left: 0; right: 0; top: 229px; text-align: center; }
  .person__name { font-size: 34px; font-weight: 700; color: var(--brand-red); line-height: 40px; }
  .person__role-row {
    position: absolute; left: 50px; right: 49px; top: 48px;
    display: flex; align-items: center; gap: 10px;
  }
  .person__rule { flex: 1; height: 1px; background: var(--brand-orange); }
  .person__role { font-size: 20px; font-weight: 500; color: var(--brand-orange); line-height: 24px; }

  .contact {
    position: absolute; top: 333px; font-size: 20px; line-height: 26.5px; color: var(--text-grey);
  }
  .contact--left { left: 50px; }
  .contact--right { right: 49px; text-align: right; }
  .contact__item { display: flex; align-items: center; gap: 10px; }
  .contact__icon { width: 20px; height: 20px; fill: var(--brand-red); }

  .band { position: absolute; bottom: 0; height: 18px; }
  .band--yellow { left: 0; width: 411px; background: var(--brand-yellow); }
  .band--red { right: 0; width: 411px; background: var(--brand-red); }

  .back__url {
    position: absolute; left: 0; right: 0; top: 404px; text-align: center;
    font-size: 19px; letter-spacing: 5px; color: var(--text-light);
  }
</style>
</head>
<body>
  <section class="card card--front">
    <div class="wordmark"><span>BrindleStaffing</span><span class="wordmark__dot"></span></div>

    <div class="person">
      <div class="person__name">Gordon Pratley</div>
      <div class="person__role-row">
        <span class="person__rule"></span>
        <span class="person__role">Chairman</span>
        <span class="person__rule"></span>
      </div>
    </div>

    <div class="contact contact--left">
      <div class="contact__item">
        <svg class="contact__icon" viewBox="0 0 20 20" aria-hidden="true"><path d="M6 1h8a1.5 1.5 0 0 1 1.5 1.5v15A1.5 1.5 0 0 1 14 19H6a1.5 1.5 0 0 1-1.5-1.5v-15A1.5 1.5 0 0 1 6 1zm0 3v11h8V4z"/></svg>
        <span>813-555-4172</span>
      </div>
      <div class="contact__item">
        <svg class="contact__icon" viewBox="0 0 20 20" aria-hidden="true"><path d="M5 2h10v5H5zM2 8h16a1 1 0 0 1 1 1v6h-3v3H4v-3H1V9a1 1 0 0 1 1-1zm4 6v2h8v-2z"/></svg>
        <span>813-555-8036</span>
      </div>
      <div class="contact__item">
        <svg class="contact__icon" viewBox="0 0 20 20" aria-hidden="true"><path d="M2 5h16v11H2zm1.5 1.5v.6L10 11l6.5-3.9v-.6z"/></svg>
        <span>gpratley@brindlestaffing.com</span>
      </div>
    </div>

    <div class="contact contact--right">
      <div>417 39th Avenue South</div>
      <div>SAINT PETERSBURG FL 33712</div>
      <div>www.brindlestaffing.com</div>
    </div>

    <div class="band band--yellow"></div>
    <div class="band band--red"></div>
  </section>

  <section class="card card--back">
    <div class="wordmark"><span>BrindleStaffing</span><span class="wordmark__dot"></span></div>
    <div class="back__url">www.brindlestaffing.com</div>
  </section>
</body>
</html>
```